Web Design For Marlow Pool Service

We are working with a company that wants a website for their pool service. Some sites to use for content/competitors and inspiration:
https://sacramento.brightwaterpoolco.example/builder/newbuild/repair/ppc
https://hollowbrookpoolcareplus.example/
https://lakemontpoolservice.example/
https://www.dravenspoolresurfacing.example/pool-renovation-ga/
Thank you for taking the time to consider designing a website for us. We are web developers based in Stockton, CA, USA. Most of our projects go through the same process. Understanding this process may help you win a project with us. We custom-code all of our websites in-house. We don’t have any requirements as to what tools you use for your design, but we prefer Figma files. For any design that we label as four-stars, we send it to the client for review. The client picks the final design they want us to use. Once we complete this process, we will continue to show additional clients all the four-star sites and purchase them later. Your designs will have multiple chances to sell. For better chances of success, we ask that you follow these guidelines.
IMAGES:
If you use any images or icons in the design, we ask that you have a link to the asset so we can purchase the image/icon. Most of the designs we submit do not have the customer’s images on them unless they have some great images. Be creative; show us the feeling you are trying to portray with your image choices. Use any royalty-free site you choose. We subscribe to Adobe and mainly use their images, but we can purchase images outside of Adobe. PLEASE NOTE: we will not submit designs to clients with watermarks on the images.
FONTS:
We ask that you identify the fonts used in the design. This can be done in a message if you want. We typically use Google Fonts and Adobe Fonts.
CONTENT:
We're always open to different content and ideas. We often submit designs with stock images so the client can see our vision. We typically take pictures after the website launch to use their images with our vision. Lorem Ipsum is fine for paragraphs, but we ask that you write the headers in correct English. We want to be able to show the vision and identify the sections of the website.
INSPIRATION:
We typically add a couple of links in the brief of websites we like to help you get started in your design.
REVISIONS:
We do not often ask for revisions of the designs unless we see something in the design that may not appeal to the client. If there are slight changes that we want to make, we do that in the development process.
FEEDBACK:
We rarely give feedback on designs during the design process. We are working on many website projects and do not have the time to provide feedback. We usually respond if your request is well thought out and asks specific questions, but a note asking “feedback, please” usually goes unanswered.
Number of Pages Required
1 page
Look and feel
Each slider illustrates characteristics of the customer's brand and the style your logo design should communicate.

```html
<!DOCTYPE html>
<html lang="en">
<head>
<meta charset="utf-8">
<title>Marlow Pool Service</title>
<link href="https://fonts.googleapis.com/css2?family=Roboto:wght@400;500;700;900&family=Montserrat:wght@600&display=swap" rel="stylesheet">
<style>
:root{
  --blue:#2f95ee;
  --blue-dark:#0b4fa6;
  --navy:#1b2333;
  --ink:#1c1c1c;
  --text:#3a3a3a;
  --pale:#e4f3f8;
  --pale-2:#eaf3fa;
  --white:#fff;
  --star:#f3c623;
}
*{box-sizing:border-box;margin:0;padding:0}
html,body{width:1200px;height:4559px;overflow:hidden;background:var(--white)}
body{font-family:"Roboto",Arial,sans-serif;color:var(--text)}
.page{position:relative;width:1200px;height:4559px}
section,header,footer{position:absolute;left:0;width:1200px}
.abs{position:absolute}
.btn{position:absolute;display:flex;align-items:center;justify-content:center;gap:10px;background:var(--blue-dark);color:var(--white);font-weight:700;font-size:14px;text-transform:uppercase;letter-spacing:.2px}
.btn svg{width:14px;height:14px}
.para{font-size:14.6px;line-height:25.7px;text-align:justify;color:var(--text)}
.section-title{position:absolute;left:0;width:1200px;text-align:center;font-weight:700;font-size:35px;color:var(--ink);text-transform:uppercase}

/* header */
.site-header{top:0;height:127px;background:var(--white);box-shadow:0 2px 6px rgba(0,0,0,.08);z-index:2}
.brand{left:112px;top:40px;display:flex;align-items:center;gap:12px}
.brand-dot{width:36px;height:36px;border-radius:50%;background:var(--blue)}
.brand-name{font-size:26px;font-weight:500;color:var(--blue-dark);line-height:1}
.search{left:593px;top:23px;width:253px;height:44px;border:1px solid #d6d6d6;display:flex;align-items:center;justify-content:space-between;padding:0 14px;font-size:13px;color:#777}
.phone-top{left:880px;top:23px;display:flex;align-items:center;gap:10px;font-size:21px;font-weight:500;color:var(--blue)}
.phone-top .ic{width:42px;height:42px;border-radius:50%;background:var(--blue);display:flex;align-items:center;justify-content:center}
.main-nav{right:111px;top:89px;display:flex;gap:0;font-size:14.5px;font-weight:500;color:var(--ink)}
.main-nav span{padding:0 22px}
.main-nav span+span{border-left:1px solid #333}
.main-nav span:last-child{padding-right:0}

/* hero */
.hero{top:127px;height:590px;background:linear-gradient(180deg,#6f8f5f 0%,#a9b8a8 30%,#d9dedb 48%,#9fc7d3 62%,#4aa6c6 80%,#7d8a8c 100%)}
.hero-img{position:absolute;inset:0}
.hero-sub{top:218px;font-size:36px;font-weight:700;color:var(--white);text-align:center;width:100%;text-shadow:0 2px 6px rgba(0,0,0,.5)}
.hero-title{top:288px;font-size:58px;font-weight:900;color:var(--white);text-align:center;width:100%;text-shadow:0 3px 8px rgba(0,0,0,.55);text-transform:uppercase}
.hero .btn{left:517px;top:381px;width:163px;height:46px;background:var(--blue);border-radius:2px}

/* about */
.about{top:717px;height:556px;background:var(--pale)}
.about-ring{left:92px;top:59px;width:450px;height:450px;border-radius:50%;background:var(--blue)}
.about-photo{left:100px;top:54px;width:446px;height:446px;border-radius:50%;background:linear-gradient(135deg,#3cb6ea 0%,#2b8cd9 40%,#c73a2f 60%,#8b8f96 100%)}
.about h2{left:596px;top:104px;font-size:35px;font-weight:700;color:var(--ink)}
.about .para{position:absolute;left:596px;top:158px;width:492px}
.about .btn{left:596px;top:414px;width:165px;height:46px}

/* services */
.services{top:1273px;height:1092px;background:var(--white)}
.services .section-title{top:82px}
.svc-title{position:absolute;font-size:28px;font-weight:500;color:var(--ink);text-transform:uppercase}
.services .para{position:absolute;width:495px}
.svc-photo{position:absolute;border:3px solid var(--white);box-shadow:0 10px 24px rgba(0,0,0,.22)}
.svc1-photo{left:665px;top:185px;width:422px;height:367px;background:linear-gradient(180deg,#a9978a 0%,#bca797 45%,#e9e9e6 62%,#49c2e0 80%,#2aa9d8 100%)}
.svc2-photo{left:110px;top:633px;width:419px;height:367px;background:linear-gradient(180deg,#c8c4b8 0%,#5b4ca2 35%,#aeb7c2 70%,#e6eaf0 100%)}

/* reviews */
.reviews{top:2365px;height:614px;background:linear-gradient(180deg,#2f8ff0 0%,#3aa1f5 100%);overflow:hidden}
.reviews .section-title{top:64px;color:var(--white);font-size:33px}
.side-card{position:absolute;top:168px;width:179px;height:341px;border-radius:18px;background:rgba(255,255,255,.25)}
.side-left{left:0;border-top-left-radius:0;border-bottom-left-radius:0}
.side-right{left:1021px;border-top-right-radius:0;border-bottom-right-radius:0}
.arrow{position:absolute;top:319px;width:28px;height:28px}
.review-card{position:absolute;left:214px;top:168px;width:772px;height:341px;border-radius:20px;background:var(--white);text-align:center}
.avatar{position:absolute;left:344px;top:46px;width:84px;height:84px;border-radius:50%;background:linear-gradient(180deg,#c9c2b8,#8a7262)}
.reviewer{position:absolute;top:142px;width:100%;font-family:"Montserrat",sans-serif;font-weight:600;font-size:27px;color:var(--ink)}
.stars{position:absolute;top:185px;width:100%;display:flex;justify-content:center;gap:3px}
.review-text{position:absolute;left:50px;top:220px;width:672px;font-size:14.5px;line-height:25.5px;color:#333}

/* gallery */
.gallery{top:2979px;height:653px;background:var(--white)}
.gallery .section-title{top:76px}
.tile{position:absolute}
.g1{left:112px;top:152px;width:447px;height:416px;background:linear-gradient(135deg,#2f9fd3,#8eb7cc 45%,#c93434 70%,#6b6d59)}
.g2{left:579px;top:152px;width:249px;height:203px;background:linear-gradient(135deg,#c4c0b3,#3fb3c0 60%,#20a0b4)}
.g3{left:839px;top:152px;width:249px;height:203px;background:linear-gradient(135deg,#5fb2e6,#2f7dc2 55%,#e6eef6)}
.g4{left:579px;top:363px;width:249px;height:204px;background:linear-gradient(180deg,#666b5f,#e3c53d 45%,#34a9d8 75%,#2b97cf)}
.g5{left:839px;top:363px;width:249px;height:204px;background:linear-gradient(180deg,#b8c6d0,#4aa8e0 50%,#1f7fc9)}

/* contact */
.contact{top:3632px;height:510px;background:var(--pale-2)}
.contact .section-title{top:58px}
.field{position:absolute;background:var(--white);font-size:13.5px;color:#222;padding:12px 13px;box-shadow:0 1px 3px rgba(0,0,0,.06)}
.contact .btn{left:519px;top:402px;width:162px;height:46px}

/* footer */
.site-footer{top:4142px;height:417px;background:var(--navy);color:var(--white)}
.footer-brand{left:112px;top:160px}
.footer-brand .brand-name{color:var(--blue)}
.vline{position:absolute;top:97px;width:1px;height:168px;background:#7b8497}
.f-head{position:absolute;top:90px;font-size:13px;font-weight:700;text-transform:uppercase}
.f-list{position:absolute;top:128px;list-style:none;font-size:13.5px}
.f-list li{height:30px;display:flex;align-items:center;gap:14px}
.f-list li::before{content:"»";color:var(--blue);font-size:15px}
.f-contact{position:absolute;left:639px;font-size:13.5px;display:flex;gap:20px;align-items:flex-start}
.f-contact .ic{width:24px;height:24px;border-radius:4px;background:#2b3548;display:flex;align-items:center;justify-content:center;flex:none}
.f-rule{position:absolute;left:112px;top:333px;width:976px;height:1px;background:#4a5367}
.copyright{position:absolute;top:362px;width:100%;text-align:center;font-size:13.5px}
</style>
</head>
<body>
<div class="page">

<header class="site-header">
  <div class="abs brand"><span class="brand-dot"></span><span class="brand-name">Marlow Pool Service</span></div>
  <div class="abs search"><span>Search</span>
    <svg width="13" height="13" viewBox="0 0 16 16"><circle cx="6.5" cy="6.5" r="5" fill="none" stroke="#555" stroke-width="2"/><line x1="10.5" y1="10.5" x2="15" y2="15" stroke="#555" stroke-width="2"/></svg>
  </div>
  <div class="abs phone-top"><span class="ic"><svg width="20" height="20" viewBox="0 0 24 24"><path fill="#fff" d="M6.6 10.8a15 15 0 0 0 6.6 6.6l2.2-2.2c.3-.3.7-.4 1-.2 1.1.4 2.3.6 3.6.6.6 0 1 .4 1 1V20c0 .6-.4 1-1 1A17 17 0 0 1 3 4c0-.6.4-1 1-1h3.5c.6 0 1 .4 1 1 0 1.3.2 2.5.6 3.6.1.3 0 .7-.2 1z"/></svg></span>+1 209 555 0147</div>
  <nav class="abs main-nav"><span>HOME</span><span>ABOUT US</span><span>WHAT WE DO</span><span>GALLERY</span><span>CONTACT US</span></nav>
</header>

<section class="hero">
  <div class="hero-img" role="img" aria-label="Photo of a backyard swimming pool beside a white two-storey house with trees and fountain jets"></div>
  <div class="abs hero-sub">WELCOME TO</div>
  <h1 class="abs hero-title">Marlow Pool Service</h1>
  <div class="btn">GET STARTED <svg viewBox="0 0 16 16"><circle cx="8" cy="8" r="8" fill="#fff"/><path d="M6.5 4.5 10 8l-3.5 3.5" fill="none" stroke="#2f95ee" stroke-width="2"/></svg></div>
</section>

<section class="about">
  <div class="abs about-ring"></div>
  <div class="abs about-photo" role="img" aria-label="Photo of a pool technician in red rolling out a blue solar pool cover"></div>
  <h2 class="abs">ABOUT US</h2>
  <p class="para">Lorem ipsum dolor sit amet, consectetur adipiscing elit, sed do eiusmod tempor incididunt ut labore et dolore magna aliqua. Ut enim ad minim veniam, quis nostrud exercitation ullamco laboris nisi ut aliquip ex ea commodo consequat. Duis aute irure dolor in reprehenderit in voluptate velit esse cillum dolore eu fugiat nulla pariatur. Excepteur sint occaecat cupidatat non proident, sunt in culpa qui officia deserunt mollit anim id est laborum.Lorem ipsum dolor sit amet, consectetur adipiscing elit, sed do eiusmod tempor incididunt ut labore et dolore magna enim ad minim veniam, quis nostrud exercitation ullamco laboris nisi.</p>
  <div class="btn">LEARN MORE <svg viewBox="0 0 16 16"><circle cx="8" cy="8" r="8" fill="#fff"/><path d="M6.5 4.5 10 8l-3.5 3.5" fill="none" stroke="#0b4fa6" stroke-width="2"/></svg></div>
</section>

<section class="services">
  <h2 class="section-title">WHAT WE DO</h2>
  <h3 class="svc-title" style="left:108px;top:192px">Pool Cleaning Services</h3>
  <p class="para" style="left:110px;top:239px">Lorem ipsum dolor sit amet, consectetur adipiscing elit, sed do eiusmod tempor incididunt ut labore et dolore magna aliqua. Ut enim ad minim veniam, quis nostrud exercitation ullamco laboris nisi ut aliquip ex ea commodo consequat. Duis aute irure dolor in reprehenderit in voluptate velit esse cillum dolore eu fugiat nulla pariatur. Excepteur sint occaecat cupidatat non proident, sunt in culpa qui officia deserunt mollit anim id est laborum.Lorem ipsum dolor sit amet, consectetur adipiscing elit, sed do eiusmod tempor incididunt ut labore et dolore magna enim ad minim veniam, quis nostrud exercitation ullamco laboris nisi.</p>
  <div class="btn" style="left:110px;top:494px;width:164px;height:47px">LEARN MORE <svg viewBox="0 0 16 16"><circle cx="8" cy="8" r="8" fill="#fff"/><path d="M6.5 4.5 10 8l-3.5 3.5" fill="none" stroke="#0b4fa6" stroke-width="2"/></svg></div>
  <div class="svc-photo svc1-photo" role="img" aria-label="Photo of a worker cleaning a pool floor with a long pole brush"></div>

  <div class="svc-photo svc2-photo" role="img" aria-label="Photo of two workers in hard hats repairing pool tiles"></div>
  <h3 class="svc-title" style="left:591px;top:640px">Swimming Pool Repair</h3>
  <p class="para" style="left:593px;top:687px">Lorem ipsum dolor sit amet, consectetur adipiscing elit, sed do eiusmod tempor incididunt ut labore et dolore magna aliqua. Ut enim ad minim veniam, quis nostrud exercitation ullamco laboris nisi ut aliquip ex ea commodo consequat. Duis aute irure dolor in reprehenderit in voluptate velit esse cillum dolore eu fugiat nulla pariatur. Excepteur sint occaecat cupidatat non proident, sunt in culpa qui officia deserunt mollit anim id est laborum.Lorem ipsum dolor sit amet, consectetur adipiscing elit, sed do eiusmod tempor incididunt ut labore et dolore magna enim ad minim veniam, quis nostrud exercitation ullamco laboris nisi.</p>
  <div class="btn" style="left:593px;top:943px;width:165px;height:47px">LEARN MORE <svg viewBox="0 0 16 16"><circle cx="8" cy="8" r="8" fill="#fff"/><path d="M6.5 4.5 10 8l-3.5 3.5" fill="none" stroke="#0b4fa6" stroke-width="2"/></svg></div>
</section>

<section class="reviews">
  <h2 class="section-title">CUSTOMER-REVIEWS</h2>
  <div class="side-card side-left"></div>
  <div class="side-card side-right"></div>
  <svg class="arrow" style="left:40px" viewBox="0 0 24 24"><path d="M15 4 7 12l8 8" fill="none" stroke="#fff" stroke-width="2.5"/></svg>
  <svg class="arrow" style="left:1132px" viewBox="0 0 24 24"><path d="M9 4l8 8-8 8" fill="none" stroke="#fff" stroke-width="2.5"/></svg>
  <div class="review-card">
    <div class="avatar" role="img" aria-label="Customer portrait photo"></div>
    <div class="reviewer">Darren Holt</div>
    <div class="stars">
      <svg width="17" height="16" viewBox="0 0 24 23"><path fill="#f3c623" d="M12 0l3.6 7.5 8.4 1-6.1 5.8 1.5 8.2L12 18.6 4.6 22.5l1.5-8.2L0 8.5l8.4-1z"/></svg>
      <svg width="17" height="16" viewBox="0 0 24 23"><path fill="#f3c623" d="M12 0l3.6 7.5 8.4 1-6.1 5.8 1.5 8.2L12 18.6 4.6 22.5l1.5-8.2L0 8.5l8.4-1z"/></svg>
      <svg width="17" height="16" viewBox="0 0 24 23"><path fill="#f3c623" d="M12 0l3.6 7.5 8.4 1-6.1 5.8 1.5 8.2L12 18.6 4.6 22.5l1.5-8.2L0 8.5l8.4-1z"/></svg>
      <svg width="17" height="16" viewBox="0 0 24 23"><path fill="#f3c623" d="M12 0l3.6 7.5 8.4 1-6.1 5.8 1.5 8.2L12 18.6 4.6 22.5l1.5-8.2L0 8.5l8.4-1z"/></svg>
    </div>
    <p class="review-text">Lorem ipsum dolor sit amet consectetur adipiscing elit sed do eiusmod tempor incididunt ut labore et dolore magna aliqua enim ad minim veniam, quis nostrud exercitation ullamco laboris nisi ut aliquip ex ea commodo consequat. Duis aute irure dolor in reprehenderit voluptate velit esse cillum dolore&nbsp; fugiat nulla pariatur Excepteur sint occaecat cupidatat .</p>
  </div>
</section>

<section class="gallery">
  <h2 class="section-title">OUR GALLERY</h2>
  <div class="tile g1" role="img" aria-label="Photo of a technician in red servicing pool pump equipment"></div>
  <div class="tile g2" role="img" aria-label="Photo of a man skimming a pool with a net"></div>
  <div class="tile g3" role="img" aria-label="Photo of a worker servicing pool machinery"></div>
  <div class="tile g4" role="img" aria-label="Photo of a worker with a robotic pool cleaner beside a pool"></div>
  <div class="tile g5" role="img" aria-label="Photo of a worker tiling an empty blue pool"></div>
</section>

<section class="contact">
  <h2 class="section-title">CONTACT US</h2>
  <div class="field" style="left:133px;top:120px;width:455px;height:39px">Enter Name:</div>
  <div class="field" style="left:609px;top:120px;width:458px;height:39px">Enter Email:</div>
  <div class="field" style="left:133px;top:182px;width:455px;height:39px">Enter Address:</div>
  <div class="field" style="left:609px;top:182px;width:458px;height:39px">Phone Number:</div>
  <div class="field" style="left:133px;top:241px;width:934px;height:118px">Message:</div>
  <div class="btn">SUBMIT NOW <svg viewBox="0 0 16 16"><circle cx="8" cy="8" r="8" fill="#fff"/><path d="M6.5 4.5 10 8l-3.5 3.5" fill="none" stroke="#0b4fa6" stroke-width="2"/></svg></div>
</section>

<footer class="site-footer">
  <div class="abs brand footer-brand"><span class="brand-dot"></span><span class="brand-name">Marlow Pool Service</span></div>
  <div class="vline" style="left:398px"></div>
  <div class="vline" style="left:589px"></div>
  <div class="vline" style="left:901px"></div>

  <div class="f-head" style="left:441px">Quick Links</div>
  <ul class="f-list" style="left:441px"><li>Home</li><li>About Us</li><li>What We Do</li><li>Gallery</li><li>Contact Us</li></ul>

  <div class="f-head" style="left:639px">Contact</div>
  <div class="f-contact" style="top:127px"><span class="ic"><svg width="12" height="14" viewBox="0 0 12 16"><path fill="#2f95ee" d="M6 0a6 6 0 0 0-6 6c0 4.5 6 10 6 10s6-5.5 6-10a6 6 0 0 0-6-6zm0 8.5A2.5 2.5 0 1 1 6 3.5a2.5 2.5 0 0 1 0 5z"/></svg></span><span style="font-size:12.5px;line-height:17px">2707 Lorem ipsum dolor sit<br>ameted consectetur ad</span></div>
  <div class="f-contact" style="top:190px;align-items:center"><span class="ic"><svg width="13" height="13" viewBox="0 0 24 24"><path fill="#2f95ee" d="M6.6 10.8a15 15 0 0 0 6.6 6.6l2.2-2.2c.3-.3.7-.4 1-.2 1.1.4 2.3.6 3.6.6.6 0 1 .4 1 1V20c0 .6-.4 1-1 1A17 17 0 0 1 3 4c0-.6.4-1 1-1h3.5c.6 0 1 .4 1 1 0 1.3.2 2.5.6 3.6.1.3 0 .7-.2 1z"/></svg></span><span style="font-size:16px;font-weight:700">+1 209 555 0147</span></div>
  <div class="f-contact" style="top:240px;align-items:center"><span class="ic"><svg width="14" height="11" viewBox="0 0 20 14"><rect width="20" height="14" rx="2" fill="#2f95ee"/><path d="M1 1l9 7 9-7" fill="none" stroke="#2b3548" stroke-width="1.6"/></svg></span><span>info@marlowpoolservice.com</span></div>

  <div class="f-head" style="left:950px">Get Connected</div>
  <ul class="f-list" style="left:950px"><li>FAQ</li><li>Terms Of Service</li><li>Privacy Policy</li><li>Cancellation</li><li>Refund Policy</li></ul>

  <div class="f-rule"></div>
  <div class="copyright">© 2024 Marlow Pool Service . All Rights Reserved</div>
</footer>

</div>
</body>
</html>
```